Stationery Design Project

I need a design that is simple, clean and modern, in square style, bold font.
The majority of the design needs to be White and Black with a splash of Red colour.
I would like a design for business cards and letter heads with the following information.
Name, Title, Phone, Fax, Email, Website and company ABN number

Target Market(s)

25 to 65 years old real estate clients

Industry/Entity Type

Business

Requirements
Must have
• All designs must incorporate Company Logo, Name, Title, Phone, Fax, Email, Website and company ABN number

```html
<!DOCTYPE html>
<html lang="en">
<head>
<meta charset="utf-8">
<title>Northgate Real Estate – Business Card</title>
<link href="https://fonts.googleapis.com/css2?family=Open+Sans:wght@400;600;700&display=swap" rel="stylesheet">
<style>
  :root {
    --backdrop: #e9e6e2;
    --card: #ffffff;
    --ink: #231f20;
    --text: #2b2b2b;
    --accent: #d7262d;
    --edge: #d9d6d2;
  }
  * { box-sizing: border-box; margin: 0; padding: 0; }
  html, body { width: 1200px; height: 402px; overflow: hidden; }
  body {
    position: relative;
    background: var(--backdrop);
    font-family: "Open Sans", Arial, sans-serif;
    color: var(--text);
  }
  .card {
    position: absolute;
    top: 57px;
    width: 511px;
    height: 292px;
    background: var(--card);
    border-radius: 28px;
    border: 1px solid var(--edge);
  }
  .card--front { left: 66px; }
  .card--back { left: 625px; }

  .brand-frame {
    position: absolute;
    border: 3px solid var(--ink);
    border-radius: 16px;
    display: flex;
    flex-direction: column;
    align-items: center;
    justify-content: center;
    text-align: center;
    color: var(--ink);
    font-weight: 700;
    text-transform: uppercase;
    line-height: 1.1;
  }
  .card--front .brand-frame {
    left: 39px; top: 24px; width: 217px; height: 121px;
    font-size: 25px; letter-spacing: 1px;
  }
  .card--back .brand-frame {
    left: 97px; top: 58px; width: 318px; height: 176px;
    border-width: 4px; border-radius: 22px;
    font-size: 37px; letter-spacing: 1.5px;
  }
  .brand-name__sub { font-size: 0.5em; letter-spacing: 0.35em; margin-top: 6px; }

  .person {
    position: absolute;
    left: 39px; top: 175px; width: 217px;
    text-align: center;
    color: var(--accent);
  }
  .person__name { font-size: 15px; font-weight: 700; line-height: 20px; }
  .person__title { font-size: 12.5px; line-height: 17px; }

  .abn {
    position: absolute;
    left: 306px; top: 118px;
    font-size: 13.5px; color: var(--text);
  }
  .contact-list {
    position: absolute;
    left: 306px; top: 161px;
    list-style: none;
    font-size: 12.5px; line-height: 16.7px;
  }
  .contact-list li { display: flex; align-items: center; gap: 4px; }
  .contact-list svg { width: 10px; height: 10px; fill: var(--accent); flex: none; }
  .address {
    position: absolute;
    left: 306px; top: 250px;
    font-size: 12.5px; line-height: 16px;
    font-style: normal;
  }
</style>
</head>
<body>
  <section class="card card--front">
    <div class="brand-frame">
      <span class="brand-name">Northgate</span>
      <span class="brand-name brand-name__sub">Real Estate</span>
    </div>

    <div class="person">
      <p class="person__name">Your name</p>
      <p class="person__title">Title</p>
    </div>

    <p class="abn">ABN: 1234567890</p>

    <ul class="contact-list">
      <li>
        <svg viewBox="0 0 10 10" aria-hidden="true"><path d="M2 0.5 L3.6 2.6 L2.7 3.6 C3.2 4.9 4.9 6.7 6.3 7.2 L7.3 6.3 L9.5 7.9 L8.3 9.6 C4.6 9.4 0.6 5.4 0.4 1.7 Z"/></svg>
        <span>123-456-7890</span>
      </li>
      <li>
        <svg viewBox="0 0 10 10" aria-hidden="true"><path d="M2.5 0.5 H7.5 V3.5 H2.5 Z M0.5 4 H9.5 V8 H8 V6.5 H2 V8 H0.5 Z M2.5 7 H7.5 V9.5 H2.5 Z"/></svg>
        <span>123-456-7890</span>
      </li>
      <li>
        <svg viewBox="0 0 10 10" aria-hidden="true"><path d="M0.5 2 H9.5 V8.5 H0.5 Z" /><path d="M0.8 2.3 L5 5.6 L9.2 2.3" fill="none" stroke="#fff" stroke-width="0.9"/></svg>
        <span>info@mailbox.com</span>
      </li>
      <li>
        <svg viewBox="0 0 10 10" aria-hidden="true"><circle cx="5" cy="5" r="4.6"/><path d="M0.6 5 H9.4 M5 0.5 C2.6 3 2.6 7 5 9.5 M5 0.5 C7.4 3 7.4 7 5 9.5" fill="none" stroke="#fff" stroke-width="0.8"/></svg>
        <span>&nbsp;www.website.com</span>
      </li>
    </ul>

    <address class="address">
      Street Name, City Name<br>
      State, City Zip Code
    </address>
  </section>

  <section class="card card--back">
    <div class="brand-frame">
      <span class="brand-name">Northgate</span>
      <span class="brand-name brand-name__sub">Real Estate</span>
    </div>
  </section>
</body>
</html>
```